Corporate Travel Technology Company needs new Business Card design

We need a new business card design to reflect our re-branded company. Our company is called tolvEn (pronounced tolvenn) and we provide Business Intelligence and mobile travel management solutions for the corporate travel industry. Our multinational customers use our solutions to manage large travel budgets and frequent travellers, as well as to save money and reduce risk. We'd like to see designs that use the blue and green palette as well as our corporate logo (attached below). The design should communicate innovation, insight, forward thinking, contemporary, trusted.

Target Market(s)

Large multinational corporates and Travel Agencies.

Industry/Entity Type

Business

Contact Information for Business Card

Rosalind Mercer
Chief Executive
tolvEn
Phone number - +61 (0)2 8134 2907
Email address - rosalind.mercer@tolven-example.com
Mobile number - +61 (0)438 516 702
www.tolven-example.com

Font styles to use
Other font styles liked:
• Please use font as close to corporate logo as possible

Colors
0255a3
0393ce
00a990
33b8a4
33a6d7
3176b5

Requirements
Must have
• Please include the words;
• Mobile Travel Management
• Accelerating Travel Business Insights
• Use corporate logo - although icon can be stylised if needed

```html
<!DOCTYPE html>
<html lang="en">
<head>
<meta charset="utf-8">
<title>tolvEn business card</title>
<link rel="stylesheet" href="https://fonts.googleapis.com/css2?family=Source+Sans+3:wght@400;600&display=swap">
<style>
  :root {
    --bg-top: #262626;
    --bg-bottom: #040404;
    --card: #ffffff;
    --brand-blue: #1aa3dc;
    --ink-slate: #3e5357;
    --ink-text: #3a3a3a;
  }
  * { margin: 0; padding: 0; box-sizing: border-box; }
  html, body { width: 1200px; height: 900px; overflow: hidden; }
  body {
    position: relative;
    background: linear-gradient(to bottom, var(--bg-top) 0%, #151515 55%, var(--bg-bottom) 100%);
    font-family: "Source Sans 3", "Myriad Pro", Arial, sans-serif;
  }
  .card {
    position: absolute;
    top: 306px;
    height: 271px;
    background: var(--card);
    border-radius: 10px;
    overflow: hidden;
  }
  .card-front { left: 149px; width: 439px; }
  .card-back  { left: 608px; width: 441px; height: 272px; }

  .brand-mark {
    position: absolute;
    border-radius: 50%;
    border: 3px solid var(--brand-blue);
  }
  .brand-name {
    position: absolute;
    color: var(--ink-slate);
    font-weight: 400;
    line-height: 1;
    letter-spacing: -0.5px;
    white-space: nowrap;
  }
  .card-front .brand-mark { left: 99px; top: 84px; width: 36px; height: 36px; }
  .card-front .brand-name { left: 26px; top: 124px; font-size: 54px; }

  .card-back .brand-mark { left: 199px; top: 26px; width: 54px; height: 54px; border-width: 4px; }
  .card-back .brand-name { left: 0; width: 100%; text-align: center; top: 82px; font-size: 86px; }

  .holder { position: absolute; left: 212px; top: 76px; }
  .holder-name { color: var(--brand-blue); font-size: 15px; font-weight: 600; line-height: 18px; }
  .holder-role { color: var(--ink-text); font-size: 12px; line-height: 15px; }

  .contact-list {
    position: absolute;
    left: 212px;
    top: 131px;
    list-style: none;
  }
  .contact-list li {
    display: flex;
    align-items: center;
    height: 16px;
    font-size: 12px;
    color: var(--ink-text);
    letter-spacing: -0.1px;
    white-space: nowrap;
  }
  .contact-list svg { width: 9px; height: 9px; margin-right: 10px; fill: var(--brand-blue); flex: none; }

  .taglines {
    position: absolute;
    left: 0;
    width: 100%;
    top: 200px;
    text-align: center;
    color: var(--brand-blue);
    font-size: 12.5px;
    font-weight: 600;
    line-height: 16px;
  }
</style>
</head>
<body>
  <section class="card card-front">
    <span class="brand-mark" aria-hidden="true"></span>
    <span class="brand-name">tolvEn</span>
    <div class="holder">
      <p class="holder-name">Rosalind Mercer</p>
      <p class="holder-role">Chief Executive</p>
    </div>
    <ul class="contact-list">
      <li><svg viewBox="0 0 10 10" aria-hidden="true"><path d="M2 0.5l2 2-1 1.3c.6 1.3 1.5 2.2 2.8 2.8l1.3-1 2 2-1.2 1.6C4.5 9 1 5.5 0.6 1.6z"/></svg>+61 (0)2 8134 2907</li>
      <li><svg viewBox="0 0 10 10" aria-hidden="true"><path d="M2.5 0h5v10h-5zM3.3 1v7h3.4V1z"/></svg>+61 (0)438 516 702</li>
      <li><svg viewBox="0 0 10 10" aria-hidden="true"><path d="M0 2h10v6H0zM0.8 2.6L5 5.6l4.2-3z" fill-rule="evenodd"/></svg>rosalind.mercer@tolven-example.com</li>
      <li><svg viewBox="0 0 10 10" aria-hidden="true"><path d="M5 0a5 5 0 1 0 0 10A5 5 0 0 0 5 0zm0 1a4 4 0 0 1 0 8 4 4 0 0 1 0-8zM1 4.5h8v1H1zM4.5 1h1v8h-1z"/></svg>www.tolven-example.com</li>
    </ul>
  </section>

  <section class="card card-back">
    <span class="brand-mark" aria-hidden="true"></span>
    <span class="brand-name">tolvEn</span>
    <div class="taglines">
      <p>Mobile Travel Management</p>
      <p>Accelerating Travel Business Insights</p>
    </div>
  </section>
</body>
</html>
```